Business card update

Opening a subsidiary of my company in the USA and need to update my logo.
Updates

Reason: Give more time to a good design.

I made a mistake on my briefing. It's only the business card. Thanks for alerting me on the mistake.

All the best

Teodoro

Target Market(s)

We are an Executive Search company and our target audience are executives in large corporations.

Industry/Entity Type

Business

Requirements
Must have
• Keep the logo. In the US the company is called Delia Brunet Executive Search.

```html
<!DOCTYPE html>
<html lang="en">
<head>
<meta charset="utf-8">
<title>Delia Brunet Executive Search – Business Card</title>
<link rel="stylesheet" href="https://fonts.googleapis.com/css2?family=Open+Sans:wght@300;400&display=swap">
<style>
  :root {
    --teal: #2aa8b2;
    --teal-deep: #2b9fa8;
    --ink: #3a3d40;
    --ink-soft: #55595c;
    --card: #ffffff;
    --card-edge: #f1f1f1;
    --ground: #e7e8e8;
  }
  * { margin: 0; padding: 0; box-sizing: border-box; }
  html, body { width: 900px; height: 1200px; overflow: hidden; }
  body { font-family: "Open Sans", Arial, sans-serif; background: var(--ground); position: relative; }

  .brand-band {
    position: absolute; left: 0; top: 0; width: 900px; height: 545px;
    background: var(--teal);
  }

  .card {
    position: absolute; background: var(--card);
    box-shadow: 0 4px 14px rgba(0,0,0,0.22);
  }
  .card-frame {
    position: absolute; inset: 10px 8px;
    border: 1.5px dotted var(--teal);
  }

  .card--hero { left: 262px; top: 130px; width: 388px; height: 250px;
    background: radial-gradient(ellipse at center, #ffffff 40%, var(--card-edge) 100%); }

  .wordmark {
    position: absolute; left: 38px; right: 38px; top: 50%;
    transform: translateY(-50%);
    display: flex; align-items: center; gap: 12px;
  }
  .wordmark-rule { flex: 1; height: 1.5px; background: var(--teal); }
  .wordmark-name {
    font-weight: 400; font-size: 21px; letter-spacing: 3px;
    color: var(--ink); white-space: nowrap;
  }

  .card--front { left: 468px; top: 755px; width: 386px; height: 236px; }
  .card--front .wordmark { left: 30px; right: 30px; }
  .card--front .wordmark-name { font-size: 20px; }

  .card--back { left: 46px; top: 755px; width: 386px; height: 236px; padding: 34px 36px; }
  .person-name { font-weight: 300; font-size: 23px; color: var(--ink); line-height: 1.2; }
  .person-role { font-size: 11px; color: var(--teal); margin-top: 4px; }
  .divider { width: 20px; height: 2px; background: var(--ink); margin: 14px 0 12px; }
  .contact-list { list-style: none; font-size: 10.5px; color: var(--teal-deep); line-height: 1.6; }
  .contact-list li::before { content: "• "; color: var(--ink-soft); }
  .contact-list .continued::before { content: ""; }
  .contact-list .continued { padding-left: 8px; }
</style>
</head>
<body>
  <section class="brand-band" role="img" aria-label="Teal backdrop with a faint repeating brand monogram pattern"></section>

  <article class="card card--hero">
    <div class="card-frame"></div>
    <div class="wordmark">
      <span class="wordmark-rule"></span>
      <span class="wordmark-name">DELIA BRUNET</span>
      <span class="wordmark-rule"></span>
    </div>
  </article>

  <article class="card card--back">
    <h1 class="person-name">Teodoro D. Brunet</h1>
    <p class="person-role">Co-Founder &amp; CEO</p>
    <div class="divider"></div>
    <ul class="contact-list">
      <li>tbrunet@dbexecutivesearch.com</li>
      <li>4870 Harbor Point Ave Suite 310</li>
      <li class="continued">Coral Vale FL 33290</li>
      <li>305 555-0148</li>
      <li>www.dbexecutivesearch.com</li>
    </ul>
  </article>

  <article class="card card--front">
    <div class="card-frame"></div>
    <div class="wordmark">
      <span class="wordmark-rule"></span>
      <span class="wordmark-name">DELIA BRUNET</span>
      <span class="wordmark-rule"></span>
    </div>
  </article>
</body>
</html>
```